Business card for a Exhibition booth fabrication company

Hi. My company would like to change our corporate name card. We are an events and Exhibition stand builder company. We would like our corporate name card to resonate what we do. I need someone to create something unique that relates to the industry that I am in. The graphic designer should be creative to incorporate the elements of my industry and try to blend in well in the design of the card. Our aim is to ensure that we are unique and our card can look different from our competitors.
Updates

Target Market(s)

Marketing and events manager from all companies

Contact Information for Business Card

The business card should have the following details:
Name
Job Title
Email
Website

Colors

Designer to choose colors to be used in the design.

Requirements
Must have
• The card must be look something that is relevant to the service that I am providing. My website is: www.velmora-buildworks.com
• You can see my website to get more information on what service that I am doing
Nice to have
• On the back of my card, I would like to have a globe image with the incorporation of my company logo. This is to indicate that my services can be done in any part of the world.

```html
<!DOCTYPE html>
<html lang="en">
<head>
<meta charset="utf-8">
<title>Velmora Buildworks — Business Card</title>
<link href="https://fonts.googleapis.com/css2?family=Montserrat:wght@500;600&family=Open+Sans:wght@400;600&family=Roboto+Condensed:wght@700&family=Noto+Serif:wght@400&display=swap" rel="stylesheet">
<style>
  :root {
    --red: #e3202b;
    --ink: #151515;
    --slate: #4a4a4a;
    --paper: #ffffff;
    --bg: #e9e9e9;
    --map: #d3d3d3;
  }
  * { margin: 0; padding: 0; box-sizing: border-box; }
  html, body { width: 1200px; height: 1200px; overflow: hidden; background: var(--bg); }
  .sheet {
    width: 1200px; height: 1200px;
    display: flex; flex-direction: column; align-items: center; justify-content: center;
    gap: 60px;
  }
  .card {
    position: relative;
    width: 860px; height: 491px;
    background: var(--paper);
    overflow: hidden;
    box-shadow: 0 10px 30px rgba(0,0,0,.18);
  }
  .card-shapes { position: absolute; inset: 0; width: 100%; height: 100%; }

  /* front */
  .holder { position: absolute; left: 46px; top: 128px; }
  .holder-name {
    font-family: "Roboto Condensed", sans-serif; font-weight: 700;
    font-size: 42px; line-height: 1; color: var(--slate);
  }
  .holder-name .first { color: var(--red); }
  .holder-title {
    font-family: "Noto Serif", serif; font-size: 20px; color: var(--ink); margin-top: 6px;
  }
  .contact-list {
    position: absolute; left: 40px; top: 226px;
    list-style: none;
    font-family: "Open Sans", sans-serif; font-size: 19px; color: #fff;
  }
  .contact-list li { display: flex; align-items: center; gap: 12px; height: 30px; white-space: nowrap; }
  .contact-icon { width: 18px; height: 18px; flex: none; }

  .brand {
    position: absolute; display: flex; align-items: center; gap: 14px;
    font-family: "Montserrat", sans-serif; font-weight: 600;
    color: var(--slate); letter-spacing: 3px; white-space: nowrap;
  }
  .brand-mark { background: var(--red); flex: none; }
  .card-front .brand { left: 430px; top: 160px; font-size: 22px; letter-spacing: 2px; }
  .card-front .brand-mark { width: 20px; height: 20px; }

  /* back */
  .world-map {
    position: absolute; left: 250px; top: 30px; width: 560px; height: 430px;
    border-radius: 50%;
    background: radial-gradient(ellipse at 50% 45%, #e4e4e4 0%, var(--map) 45%, rgba(211,211,211,0) 70%);
  }
  .card-back .brand { left: 50%; top: 50%; transform: translate(-50%, -50%); font-size: 36px; color: #3a3a3a; }
  .card-back .brand-mark { width: 30px; height: 30px; }
</style>
</head>
<body>
<main class="sheet">

  <section class="card card-front" aria-label="Business card front">
    <svg class="card-shapes" viewBox="0 0 860 491" aria-hidden="true">
      <polygon points="150,40 390,0 420,0 400,32 160,72" fill="var(--red)"/>
      <polygon points="250,70 440,38 400,100 230,128" fill="var(--red)"/>
      <polygon points="0,212 500,212 460,300 0,300" fill="var(--ink)"/>
      <polygon points="300,300 620,262 640,290 320,328" fill="var(--ink)"/>
      <polygon points="330,330 680,300 690,320 340,348" fill="var(--ink)"/>
      <polygon points="190,372 460,350 450,368 180,390" fill="var(--red)"/>
      <polygon points="250,398 750,356 700,430 270,440" fill="var(--red)"/>
      <polygon points="480,455 700,440 860,400 860,491 560,491" fill="var(--red)"/>
    </svg>

    <div class="holder">
      <p class="holder-name"><span class="first">Daniel</span> Reyes</p>
      <p class="holder-title">Director</p>
    </div>

    <ul class="contact-list">
      <li>
        <svg class="contact-icon" viewBox="0 0 20 20" aria-hidden="true">
          <rect x="1" y="4" width="18" height="12" rx="1" fill="var(--red)"/>
          <polyline points="2,5 10,11 18,5" fill="none" stroke="#fff" stroke-width="1.6"/>
        </svg>
        username@velmora-buildworks.com
      </li>
      <li>
        <svg class="contact-icon" viewBox="0 0 20 20" aria-hidden="true">
          <circle cx="10" cy="10" r="9" fill="var(--red)"/>
          <g fill="none" stroke="var(--ink)" stroke-width="1.2">
            <ellipse cx="10" cy="10" rx="4" ry="9"/>
            <line x1="1" y1="10" x2="19" y2="10"/>
            <line x1="3" y1="5.5" x2="17" y2="5.5"/>
            <line x1="3" y1="14.5" x2="17" y2="14.5"/>
          </g>
        </svg>
        www.velmora-buildworks.com
      </li>
    </ul>

    <div class="brand"><span class="brand-mark"></span>VELMORA BUILDWORKS</div>
  </section>

  <section class="card card-back" aria-label="Business card back">
    <div class="world-map" role="img" aria-label="Faint grey world map globe showing the continents"></div>
    <div class="brand"><span class="brand-mark"></span>VELMORA BUILDWORKS</div>
  </section>

</main>
</body>
</html>
```